jQuery Mobile CSS for web app

Task Outline:
Create jQuery Mobile themeroller compliant CSS and icons for a mobile web app.
Task Description:
Brindle Solutions are in the process of implementing a new, web based version of their Tessel operations platform.
The web based version of Tessel is built on top of the jQuery Mobile platform and we are looking for a designer to create a jQuery Mobile themeroller compliant CSS theme pack that we can plug into our application. The aim is to remove the standard jQuery Mobile look and feel and to introduce the Brindle branding throughout the new web app.
A number of screenshots are shown in the attached design spec (brindle_solutions.pdf) that show what the current (Windows Mobile 6.5) application looks like, alongside the development version of our new web app.
Deliverables:
• jQuery Mobile (v 1.4.2) themeroller compliant CSS which provides theming for all jQuery Mobile UI components.
• Example html showing how to use the CSS theme (especially where additional html/css classes are required).
• New set of status icons (as listed in attachment)
Inspiration:
See our website for current branding: www.brindle-solutions-demo.net

```html
<!DOCTYPE html>
<html lang="en">
<head>
<meta charset="utf-8">
<title>Halden – Crew</title>
<link rel="stylesheet" href="https://fonts.googleapis.com/css2?family=Roboto:wght@400;500&display=swap">
<style>
  :root {
    --bar-top: #3c3c3c;
    --bar-bottom: #121212;
    --bar-text: #ffffff;
    --row-bg: #f1f2f4;
    --row-line: #c4c6c9;
    --row-text: #2a2a2a;
    --page-bg: #d6d6d6;
    --footer-bg: #262626;
    --btn-top: #7a8290;
    --btn-bottom: #4a5261;
    --menu-bg: #1b1b1b;
    --menu-bar: #bdbdbd;
  }
  * { box-sizing: border-box; margin: 0; padding: 0; }
  html, body { width: 928px; height: 1200px; overflow: hidden; }
  body {
    font-family: "Roboto", Arial, sans-serif;
    background: var(--page-bg);
    position: relative;
  }
  .app-header {
    position: absolute; left: 0; top: 0; width: 928px; height: 132px;
    background: linear-gradient(var(--bar-top), var(--bar-bottom));
    display: flex; align-items: center; justify-content: center;
    box-shadow: 0 3px 6px rgba(0,0,0,.35);
    z-index: 2;
  }
  .app-title {
    color: var(--bar-text); font-size: 44px; font-weight: 500;
  }
  .crew-list {
    position: absolute; left: 0; top: 132px; width: 920px;
    list-style: none;
  }
  .crew-item {
    height: 192px;
    background: var(--row-bg);
    border-bottom: 3px solid var(--row-line);
    border-right: 2px solid var(--row-line);
    box-shadow: 0 2px 4px rgba(0,0,0,.18);
    display: flex; align-items: center;
    padding-left: 60px;
    font-size: 40px; color: var(--row-text);
  }
  .app-footer {
    position: absolute; left: 0; top: 1041px; width: 928px; height: 159px;
    background: var(--footer-bg);
  }
  .back-button {
    position: absolute; left: 45px; top: 37px;
    width: 205px; height: 82px;
  }
  .back-button svg { position: absolute; left: 0; top: 0; }
  .back-label {
    position: absolute; left: 70px; top: 0; height: 82px;
    display: flex; align-items: center;
    color: #fff; font-size: 38px; font-weight: 500;
  }
  .menu-button {
    position: absolute; left: 395px; top: 14px; width: 138px; height: 126px;
    background: var(--menu-bg);
    display: flex; flex-direction: column; align-items: center; justify-content: center; gap: 12px;
  }
  .menu-button span {
    display: block; width: 72px; height: 14px; background: var(--menu-bar);
  }
  .screen-code {
    position: absolute; right: 8px; bottom: 10px;
    color: #fff; font-size: 28px;
  }
</style>
</head>
<body>
  <header class="app-header">
    <h1 class="app-title">Halden</h1>
  </header>

  <ul class="crew-list">
    <li class="crew-item">2 x Field Foreman</li>
    <li class="crew-item">1 x Master Electrician</li>
    <li class="crew-item">2 x Field Supervisor</li>
    <li class="crew-item">10 x Pusher</li>
  </ul>

  <footer class="app-footer">
    <div class="back-button">
      <svg width="205" height="82" viewBox="0 0 205 82">
        <defs>
          <linearGradient id="backFill" x1="0" y1="0" x2="0" y2="1">
            <stop offset="0" stop-color="#7a8290"/>
            <stop offset="1" stop-color="#4a5261"/>
          </linearGradient>
        </defs>
        <path d="M0 41 L38 2 H197 Q204 2 204 9 V73 Q204 80 197 80 H38 Z" fill="url(#backFill)" stroke="#1a1d22" stroke-width="2"/>
      </svg>
      <span class="back-label">Back</span>
    </div>
    <div class="menu-button" aria-label="Menu"><span></span><span></span><span></span></div>
    <div class="screen-code">C6</div>
  </footer>
</body>
</html>
```